Luxury Real Estate Website, Midwest, United States

We need web design services for a luxury website. We need IDX Integration with our MLS. We want this to be a very simple website with amazing graphics. We want it to link up with our MailChimp account in order to generate leads through a "More Information" Pop up on the main page. We want the main page to be covered with one large graphic that is a rolling slideshow of active listings of $400,000 and up from the IDX Integration. We need this website to give a very exclusive and sleek look. Lots of black is good... I will upload our logos in Black and Silver. We will also need an "About" page that we are going to call "Qeno Info". We want our graphics to be extremely impressive. Keep in mind, we are a company in the Midwest of the United States, and our real estate has a different look than homes in California or Florida. We need graphics that are realistic for the Midwest, yet still high-end.
Target Market(s)
Luxury Homeowners in the Midwest United States. The graphics needs to be pristine.
Industry/Entity Type
Real Estate
Coding
Coded - Design and coding required
Number of Pages Required
3 page
Requirements
Must have
- Large graphics with IDX Integration. The photos of real estate need to represent real estate that is common in the Midwest, United States. We also need MailChimp integration. We need a pop up that is titled "My Free Market Analysis" that makes them fill out a contact form asking for Full Name, Email Address, Phone Number and Address. This needs to be a pop up on the front page and will integrate with our MailChimp account. We also need a page called "About Qe No Home". And another page where clients can download informational PDFs. The main component needs to be a front page search engine connected with the IDX to access active listings from our MLS. I attached our logos and a sample front page of a website. I would love for ours to look similar.
Nice to have
- Lake House photos on midwest lakes are a plus.
Should not have
- Should not have clutter. This website needs to be clean, luxurious and exclusive.

```html
<!DOCTYPE html>
<html lang="en">
<head>
<meta charset="utf-8">
<title>Hearthside Realty Group</title>
<link rel="stylesheet" href="https://fonts.googleapis.com/css2?family=Lato:wght@400;700&family=Open+Sans:ital,wght@0,400;1,400&display=swap">
<style>
:root{
  --ink:#2b2b2b;
  --ink-soft:#555555;
  --muted:#8a8a8a;
  --white:#ffffff;
  --sky-top:#b9cfe8;
  --sky-bottom:#f4f7fb;
  --band:#b3b3b3;
  --band-light:#dcdcdc;
  --caption:#3d3d3d;
  --caption-sub:#bdbdbd;
  --footer:#ebebeb;
  --line:#444444;
  --footer-brand:#9a9a9a;
  --social:#6a6a6a;
}
*{box-sizing:border-box;margin:0;padding:0}
html,body{width:1200px;height:2546px;overflow:hidden;background:var(--white)}
body{position:relative;font-family:"Open Sans",Arial,sans-serif;color:var(--ink)}

/* Header */
.site-header{position:absolute;left:0;top:0;width:1200px;height:96px;background:var(--white);z-index:2}
.brand{position:absolute;left:127px;top:34px;white-space:nowrap;font-family:"Lato",Arial,sans-serif;font-weight:400;font-size:22px;letter-spacing:1px;color:var(--ink);text-transform:uppercase}
.main-nav{position:absolute;top:42px;left:463px;display:flex;font-family:"Lato",Arial,sans-serif;font-size:14.5px;text-transform:uppercase;color:var(--ink-soft);white-space:nowrap}
.main-nav a{color:inherit;text-decoration:none;margin-right:32px}
.main-nav a.active{color:#111}

/* Hero */
.hero{position:absolute;left:0;top:96px;width:1200px;height:630px;
  background:
    linear-gradient(180deg,rgba(20,30,45,.18) 0%,rgba(20,30,45,0) 45%,rgba(20,30,20,.15) 100%),
    linear-gradient(180deg,#6f8fb6 0%,#98b0cb 26%,#9a8572 50%,#7a6a56 62%,#5f7448 80%,#4c5f3e 100%)}
.hero-title{position:absolute;top:124px;width:100%;text-align:center;font-family:"Lato",Arial,sans-serif;font-weight:700;font-size:41px;color:var(--white);text-transform:uppercase;text-shadow:0 1px 4px rgba(0,0,0,.35)}
.hero-sub{position:absolute;top:176px;width:100%;text-align:center;font-family:"Lato",Arial,sans-serif;font-weight:400;font-size:28px;letter-spacing:.5px;color:var(--white);text-transform:uppercase;text-shadow:0 1px 4px rgba(0,0,0,.35)}
.slider-dots{position:absolute;left:1086px;top:230px;display:flex;flex-direction:column;gap:10px}
.slider-dots span{width:14px;height:14px;border-radius:50%;background:var(--white)}
.slider-dots span.current{background:transparent;border:2px solid var(--white)}

/* Sky section */
.intro{position:absolute;left:0;top:726px;width:1200px;height:676px;background:linear-gradient(180deg,var(--sky-top) 0%,#d6e2f0 50%,var(--sky-bottom) 100%)}

.service-card{position:absolute;top:624px;width:309px;height:235px;background:var(--white);border-radius:3px;box-shadow:0 2px 6px rgba(0,0,0,.18);text-align:center;z-index:3}
.service-card svg{position:absolute;left:50%;top:28px;transform:translateX(-50%)}
.service-card h3{position:absolute;top:104px;width:100%;font-family:"Lato",Arial,sans-serif;font-weight:700;font-size:18px;color:var(--ink);text-transform:uppercase}
.service-card p{position:absolute;top:140px;left:34px;right:34px;font-size:11.5px;line-height:21px;color:var(--ink-soft)}

.about-photo{position:absolute;left:117px;top:977px;width:475px;height:306px;background:linear-gradient(180deg,#7fa6d2 0%,#a9c0d6 34%,#a07a5e 50%,#6e8f4e 64%,#8aa3b8 82%,#5f7a8c 100%)}
.about-frame{position:absolute;left:501px;top:944px;width:584px;height:375px;border:1.5px solid #666}
.about-copy{position:absolute;left:628px;top:996px;width:430px}
.about-copy h2{font-family:"Lato",Arial,sans-serif;font-weight:400;font-size:33px;line-height:38px;color:var(--ink);text-transform:uppercase}
.about-copy h2 small{display:block;font-size:25px;line-height:32px}
.about-copy p{font-size:12.5px;line-height:21px;color:var(--ink-soft);margin-top:14px}
.about-copy p + p{margin-top:12px}
.btn-outline{position:absolute;left:628px;top:1227px;width:155px;height:41px;border:2px solid var(--line);font-family:"Lato",Arial,sans-serif;font-weight:700;font-size:15px;line-height:37px;text-align:center;text-transform:uppercase;color:var(--ink);text-decoration:none}

/* Featured */
.featured{position:absolute;left:0;top:1402px;width:1200px;height:499px;background:var(--band)}
.band-edge{position:absolute;left:0;top:1380px;z-index:1}
.section-title{position:absolute;width:100%;text-align:center;font-family:"Lato",Arial,sans-serif;font-weight:400;font-size:25px;color:var(--ink);text-transform:uppercase;letter-spacing:.5px}
.property-tile{position:absolute;top:1509px;width:228px;height:309px}
.property-tile .photo{position:absolute;left:0;top:0;width:100%;height:239px}
.property-tile .caption{position:absolute;left:0;top:239px;width:100%;height:70px;background:var(--caption);padding:12px 0 0 20px}
.property-tile h4{font-family:"Lato",Arial,sans-serif;font-weight:400;font-size:17px;color:var(--white)}
.property-tile span{display:block;font-size:11px;color:var(--caption-sub);margin-top:2px}
.property-tile .corner{position:absolute;right:6px;bottom:6px}

/* Testimonials */
.testimonial{position:absolute;top:2045px;width:296px;height:188px;background:var(--white);border:1px solid #d8d8d8;border-radius:6px;box-shadow:0 2px 6px rgba(0,0,0,.15);padding:20px 28px 0 58px}
.testimonial .quote-mark{position:absolute;left:22px;top:18px;font-family:Georgia,serif;font-size:48px;line-height:48px;color:#c4c4c4}
.testimonial p{font-style:italic;font-size:12.5px;line-height:25px;color:var(--muted)}
.author{position:absolute;top:2247px;height:52px}
.author .avatar{position:absolute;left:0;top:0;width:50px;height:50px;border-radius:50%;background:linear-gradient(160deg,#b8a08a,#7a6656)}
.author strong{position:absolute;left:63px;top:5px;white-space:nowrap;font-family:"Lato",Arial,sans-serif;font-weight:400;font-size:14px;color:#111}
.author span{position:absolute;left:63px;top:28px;white-space:nowrap;font-size:11.5px;color:var(--muted)}

/* Footer */
.site-footer{position:absolute;left:0;top:2385px;width:1200px;height:161px;background:var(--footer)}
.footer-brand{position:absolute;left:122px;top:56px;white-space:nowrap;font-family:"Lato",Arial,sans-serif;font-weight:400;font-size:20px;letter-spacing:1px;color:var(--footer-brand);text-transform:uppercase}
.footer-nav{position:absolute;left:402px;top:54px;white-space:nowrap;font-family:"Lato",Arial,sans-serif;font-size:13px;color:var(--ink-soft);text-transform:uppercase}
.footer-nav a{color:inherit;text-decoration:none;margin-right:27px}
.copyright{position:absolute;left:402px;top:83px;white-space:nowrap;font-size:12px;color:var(--ink-soft)}
.social{position:absolute;left:975px;top:55px;display:flex;gap:24px}
.social span{width:14px;height:14px;border-radius:50%;background:var(--social)}
</style>
</head>
<body>

<header class="site-header">
  <div class="brand">Hearthside Realty</div>
  <nav class="main-nav">
    <a class="active" href="#">Home</a>
    <a href="#">Qeno Info</a>
    <a href="#">About Qe No Home</a>
    <a href="#">Downloads</a>
    <a href="#">Contact Us</a>
  </nav>
</header>

<section class="hero" role="img" aria-label="Slideshow of a brick lakeside house with gabled roofs beside calm water and green trees">
  <h1 class="hero-title">Welcome to Hearthside Realty Group</h1>
  <p class="hero-sub">Vivamus porttitor purus eleifend</p>
  <div class="slider-dots"><span class="current"></span><span></span><span></span><span></span></div>
</section>

<section class="intro"></section>

<article class="service-card" style="left:117px">
  <svg width="56" height="56" viewBox="0 0 56 56" fill="none" stroke="#555" stroke-width="2"><path d="M6 26 L28 8 L50 26"/><path d="M11 22 V50 H45 V22"/><rect x="22" y="34" width="12" height="16"/><rect x="14" y="28" width="6" height="6"/><rect x="36" y="28" width="6" height="6"/></svg>
  <h3>Luxury Property</h3>
  <p>Class aptent taciti sociosqu ad litora torquent per conubia nostra per inceptos hymenaeos Proin nulla arcu</p>
</article>
<article class="service-card" style="left:446px">
  <svg width="56" height="56" viewBox="0 0 56 56" fill="none" stroke="#555" stroke-width="2"><path d="M12 22 L28 8 L44 22"/><path d="M16 19 V36 H40 V19"/><rect x="24" y="26" width="8" height="10"/><path d="M6 44 H20 L30 48 H48"/><path d="M6 50 H50"/></svg>
  <h3>Buy &amp; Selling</h3>
  <p>Class aptent taciti sociosqu ad litora torquent per conubia nostra per inceptos hymenaeos Proin nulla arcu</p>
</article>
<article class="service-card" style="left:774px">
  <svg width="56" height="56" viewBox="0 0 56 56" fill="none" stroke="#555" stroke-width="2"><circle cx="20" cy="30" r="7"/><path d="M6 52 C6 42 34 42 34 52 Z"/><path d="M30 6 H52 V22 H40 L34 27 V22 H30 Z"/><path d="M38 11 C38 8 44 8 44 11 C44 14 41 14 41 17"/></svg>
  <h3>Qeno Info</h3>
  <p>Class aptent taciti sociosqu ad litora torquent per conubia nostra per inceptos hymenaeos Proin nulla arcu</p>
</article>

<div class="about-frame"></div>
<div class="about-photo" role="img" aria-label="Brick country house with a dark roof reflected in a pond, surrounded by trees"></div>
<div class="about-copy">
  <h2>About Hearthside<small>Realty Group</small></h2>
  <p>Praesent elementum elit at tellus nec ultricies sit amet porttitor mattis enim In massa libero interdum nec interdum vel blandit sed nulla</p>
  <p>In ullamcorper est eget tempor cursus neque mi consectetuer mi a ultricies massa est sed nisl Class aptent taciti sociosqu ad litora torquent per conubia nostra per inceptos hymenaeos Proin nulla</p>
</div>
<a class="btn-outline" href="#">Read More</a>

<svg class="band-edge" width="1200" height="24" viewBox="0 0 1200 24">
  <path d="M0 22 Q300 4 530 6 L600 22 L670 6 Q900 4 1200 22 L1200 24 L0 24 Z" fill="var(--band-light)"/>
</svg>
<section class="featured"></section>
<h2 class="section-title" style="top:1453px">Featured Property</h2>

<article class="property-tile" style="left:117px">
  <div class="photo" role="img" aria-label="Red wooden lake house among green trees" style="background:linear-gradient(180deg,#4e6b3c 0%,#8a4a3c 55%,#3e4d34 100%)"></div>
  <div class="caption"><h4>Property Title</h4><span>Dictum eget fermentum et lorem</span></div>
  <svg class="corner" width="8" height="8"><path d="M8 0 V8 H0" fill="none" stroke="#fff" stroke-width="2"/></svg>
</article>
<article class="property-tile" style="left:363px">
  <div class="photo" role="img" aria-label="White lakeside cottage with a sunlit porch" style="background:linear-gradient(180deg,#6c93c2 0%,#8a9a92 40%,#e2e4e2 75%,#b6bab2 100%)"></div>
  <div class="caption"><h4>Property Title</h4><span>Dictum eget fermentum et lorem</span></div>
  <svg class="corner" width="8" height="8"><path d="M8 0 V8 H0" fill="none" stroke="#fff" stroke-width="2"/></svg>
</article>
<article class="property-tile" style="left:611px">
  <div class="photo" role="img" aria-label="Dark gabled house with white trim at dusk" style="background:linear-gradient(180deg,#7d97b2 0%,#55636f 55%,#44533c 100%)"></div>
  <div class="caption"><h4>Property Title</h4><span>Dictum eget fermentum et lorem</span></div>
  <svg class="corner" width="8" height="8"><path d="M8 0 V8 H0" fill="none" stroke="#fff" stroke-width="2"/></svg>
</article>
<article class="property-tile" style="left:857px">
  <div class="photo" role="img" aria-label="Cottage by a river at sunset with trees" style="background:linear-gradient(180deg,#4a5a36 0%,#c9a066 45%,#4a3a2c 100%)"></div>
  <div class="caption"><h4>Property Title</h4><span>Dictum eget fermentum et lorem</span></div>
  <svg class="corner" width="8" height="8"><path d="M8 0 V8 H0" fill="none" stroke="#fff" stroke-width="2"/></svg>
</article>

<h2 class="section-title" style="top:1982px">Testimonials</h2>

<blockquote class="testimonial" style="left:105px"><span class="quote-mark">&ldquo;</span><p>Morbi diam mauris viverra in gravida eu mattis in ante Morbi eget arcu Morbi porta libero id ullamcorper nonummy nibh ligula pulvinar metus eget</p></blockquote>
<blockquote class="testimonial" style="left:440px"><span class="quote-mark">&ldquo;</span><p>Morbi diam mauris viverra in gravida eu mattis in ante Morbi eget arcu Morbi porta libero id ullamcorper nonummy nibh ligula pulvinar metus eget</p></blockquote>
<blockquote class="testimonial" style="left:774px"><span class="quote-mark">&ldquo;</span><p>Morbi diam mauris viverra in gravida eu mattis in ante Morbi eget arcu Morbi porta libero id ullamcorper nonummy nibh ligula pulvinar metus eget</p></blockquote>

<div class="author" style="left:115px"><div class="avatar" role="img" aria-label="Portrait of the reviewer"></div><strong>By Author Name</strong><span>City Location</span></div>
<div class="author" style="left:450px"><div class="avatar" role="img" aria-label="Portrait of the reviewer"></div><strong>By Author Name</strong><span>City Location</span></div>
<div class="author" style="left:784px"><div class="avatar" role="img" aria-label="Portrait of the reviewer"></div><strong>By Author Name</strong><span>City Location</span></div>

<footer class="site-footer">
  <div class="footer-brand">Hearthside Realty</div>
  <nav class="footer-nav">
    <a href="#">Home</a><a href="#">Qeno Info</a><a href="#">About Qe No Home</a><a href="#">Downloads</a><a href="#">Contact Us</a>
  </nav>
  <p class="copyright">&copy; 2018 Company Name &nbsp;All right reserved</p>
  <div class="social" aria-label="Social links"><span></span><span></span><span></span></div>
</footer>

</body>
</html>
```